Audio Visual company needs WordPress Site re-design

We need a new, simple and sleek redesign of our website, www.kelvarosupply.net. It is crucial that it is mobile platform friendly! The company emphasis is on commercial sound and video installation.

Examples of what our company does can be found here: http://bramwickav.org/

I am NOT looking for a storefront or an e-commerce site. I would just like an elegant site that describes our services. Perhaps incorporate a sleek showcase into the homepage of projects we have completed. Also would like an elegant menu-bar, perhaps enhance our current site menu or similar.

Here is a link to another site that exhibits the content I am looking for. Their target market is also much like mine.
http://www.pollanderhouse.com/ ........ A polished up version of this site would probably be my ideal site. It has almost EXACTLY the content I am looking for. Exclude the "Printing & signage" category. Needs nicer menus, contact page and project showcase.

Here is another example: http://www.clearhavenmedia.com/ ......... This site has a very nice homepage design with a good layout and feature slider. The site is simple, elegant and to the point.

Target Market(s)

Corporate/commercial business, Educational institutions

Industry/Entity Type

E-Commerce

Font styles to use
Serif
Sans Serif

Requirements
Must have
• Mobile friendly navigation
Nice to have
• HTML5 & CSS3
Should not have
• No Adobe Flash content. No store templates or e-commerce. We are a service based company not a product sales company

```html
<!DOCTYPE html>
<html lang="en">
<head>
<meta charset="utf-8">
<title>Kelvaro Supply — Sound &amp; Video Solutions</title>
<link rel="stylesheet" href="https://fonts.googleapis.com/css2?family=Open+Sans:wght@400;600;700&display=swap">
<style>
:root{
  --red:#c4161c;
  --ink:#222;
  --body:#666;
  --muted:#999;
  --line:#e3e3e3;
  --dark:#262626;
  --paper:#fff;
}
*{box-sizing:border-box;margin:0;padding:0}
html,body{width:839px;height:1200px;overflow:hidden;background:var(--paper)}
body{font-family:"Open Sans",Arial,sans-serif;color:var(--body);font-size:10px;line-height:1.5;position:relative}

/* header */
.site-header{height:84px;display:flex;align-items:center;justify-content:space-between;padding:0 26px 0 42px;border-bottom:1px solid var(--line)}
.brand{display:flex;align-items:center;gap:8px}
.brand-mark{width:14px;height:14px;background:var(--red)}
.brand-name{font-size:24px;font-weight:700;color:var(--red);letter-spacing:-.3px}
.main-nav{display:flex;gap:10px}
.main-nav a{font-size:12px;color:var(--ink);text-decoration:none;padding:8px 18px;border:1px solid transparent}
.main-nav a.is-current{border-color:var(--red);color:var(--red)}

/* hero */
.hero{height:366px;position:relative;display:flex;align-items:center;justify-content:center;
  background:radial-gradient(ellipse at 70% 75%,#6a6a6a 0%,#3a3a3a 40%,#1b1b1b 80%)}
.hero-text{position:relative;width:560px;color:#fff;font-size:20px;line-height:1.35;font-weight:400;text-align:left;margin-top:-20px}

/* section heads */
.section-title{font-size:19px;font-weight:400;color:var(--ink);margin-bottom:12px}
.col-title{font-size:17px;font-weight:400;color:var(--ink);margin-bottom:10px}

.services{padding:18px 27px 0 42px}
.services-grid{display:grid;grid-template-columns:300px 216px 212px;column-gap:22px;row-gap:10px}
.feature{grid-row:span 2}
.feature-media{height:148px;position:relative;background:linear-gradient(135deg,#1d3f8a,#3f8ad8 50%,#123066)}
.feature-badge{position:absolute;left:0;bottom:-12px;width:24px;height:24px;background:var(--red)}
.feature h3{font-size:14px;font-weight:600;color:var(--ink);margin:16px 0 4px 30px}
.feature p{margin:0 0 8px 30px;width:230px}

.service-card{display:flex;gap:10px;height:120px}
.service-thumb{width:100px;height:100px;flex:none}
.service-card h3{font-size:11px;font-weight:600;color:var(--ink);margin-bottom:3px}
.service-card p{font-size:8.5px;line-height:1.45;margin-bottom:6px}

.btn{display:inline-block;background:var(--red);color:#fff;font-size:9px;padding:4px 10px;text-decoration:none}
.more{text-align:right;font-size:9px;color:var(--muted);margin-top:-18px}

.t-live{background:linear-gradient(135deg,#2c2c2c,#8a7a5a)}
.t-theater{background:linear-gradient(135deg,#3d2a1c,#b9894f)}
.t-remote{background:linear-gradient(135deg,#111,#4a6a9a)}
.t-network{background:linear-gradient(135deg,#ddd,#8a8a8a)}

/* trio */
.trio{display:grid;grid-template-columns:350px 170px 196px;column-gap:26px;padding:20px 27px 0 42px}
.about p{margin-bottom:8px;font-size:9.5px}
.media-list{list-style:none}
.media-item{display:flex;gap:9px;align-items:center;margin-bottom:12px}
.media-thumb{width:48px;height:38px;flex:none}
.media-item strong{display:block;font-size:10.5px;font-weight:600;color:var(--ink)}
.media-item span{font-size:8px;color:var(--red);font-style:italic}
.m1{background:linear-gradient(135deg,#444,#bbb)}
.m2{background:linear-gradient(135deg,#7a5a3a,#d9b48a)}
.m3{background:linear-gradient(135deg,#222,#777)}

/* reviews */
.reviews{padding:18px 27px 0 42px}
.review-grid{display:grid;grid-template-columns:repeat(3,1fr);column-gap:26px}
.review h3{font-size:12px;font-weight:700;color:var(--red);display:flex;gap:8px;align-items:center}
.review-meta{font-size:8px;color:var(--muted);margin:3px 0 6px 20px;display:flex;gap:12px}
.review p{margin-left:20px;font-size:9px}

/* footer */
.to-top{position:absolute;right:24px;bottom:74px;font-size:8px;color:var(--muted)}
.site-footer{position:absolute;left:0;right:0;bottom:0;height:66px;background:var(--dark);color:#aaa;font-size:8.5px;display:flex;align-items:center;justify-content:center}
</style>
</head>
<body>

<header class="site-header">
  <div class="brand"><span class="brand-mark"></span><span class="brand-name">Kelvaro Supply</span></div>
  <nav class="main-nav">
    <a href="#" class="is-current">Home</a>
    <a href="#">Services</a>
    <a href="#">Contact Us</a>
    <a href="#">Customer Reviews</a>
  </nav>
</header>

<section class="hero" role="img" aria-label="Dark photo of an audio mixing console with DJ turntable">
  <p class="hero-text">We specialize in the design and installation of residential &amp; commercial sound systems, HD video displays, digital projection &amp; digital signage</p>
</section>

<section class="services">
  <h2 class="section-title">Our Services</h2>
  <div class="services-grid">
    <article class="feature">
      <div class="feature-media" role="img" aria-label="Wall of digital signage screens"><span class="feature-badge"></span></div>
      <h3>Digital Media Signage</h3>
      <p>Fusce at lorem quis augue tincidunt pretium. Donec sagittis nunc in elit suscipit.</p>
      <a class="btn" href="#" style="margin-left:30px">Read More</a>
    </article>
    <article class="service-card">
      <div class="service-thumb t-live" role="img" aria-label="Live sound stage equipment"></div>
      <div><h3>Live-Sound Integration</h3><p>Sed quis tempus facilisis turpis, sit amet pretium justo mattis nec donec feugiat.</p><a class="btn" href="#">Read More</a></div>
    </article>
    <article class="service-card">
      <div class="service-thumb t-theater" role="img" aria-label="Home theater room"></div>
      <div><h3>Home Theaters</h3><p>Sed quis tempus facilisis turpis, sit amet pretium justo mattis nec donec feugiat.</p><a class="btn" href="#">Read More</a></div>
    </article>
    <article class="service-card">
      <div class="service-thumb t-remote" role="img" aria-label="Universal remote control"></div>
      <div><h3>Universal Remotes</h3><p>Sed quis tempus facilisis turpis, sit amet pretium justo mattis nec donec feugiat.</p><a class="btn" href="#">Read More</a></div>
    </article>
    <article class="service-card">
      <div class="service-thumb t-network" role="img" aria-label="Wireless network router"></div>
      <div><h3>Networking &amp; WiFi</h3><p>Sed quis tempus facilisis turpis, sit amet pretium justo mattis nec donec feugiat.</p><a class="btn" href="#">Read More</a></div>
    </article>
  </div>
  <p class="more">[ More ]</p>
</section>

<section class="trio">
  <div class="about">
    <h2 class="col-title">About Us</h2>
    <p>Ut in rhoncus nisi, ut porttitor ligula. Vivamus non sapien nisi lacus euismod blandit id ligula leo. Suspendisse potenti. Aliquam venenatis mauris elit, vel scelerisque massa mattis ac. Nam dignissim aliquet quam, tempor sodales ipsum.</p>
    <p>Duis et erat id nibh volutpat vehicula. In hac habitasse platea dictumst. Sed blandit vestibulum nulla, nec fringilla nunc lacinia eu.</p>
    <a class="btn" href="#">Read More</a>
  </div>
  <div>
    <h2 class="col-title">Audios</h2>
    <ul class="media-list">
      <li class="media-item"><div class="media-thumb m1" role="img" aria-label="Audio project photo"></div><div><strong>Curabitur ornare</strong><span>August 3rd, 2015</span></div></li>
      <li class="media-item"><div class="media-thumb m2" role="img" aria-label="Audio project photo"></div><div><strong>Curabitur ornare</strong><span>August 3rd, 2015</span></div></li>
      <li class="media-item"><div class="media-thumb m3" role="img" aria-label="Audio project photo"></div><div><strong>Curabitur ornare</strong><span>August 3rd, 2015</span></div></li>
    </ul>
  </div>
  <div>
    <h2 class="col-title">Videos</h2>
    <ul class="media-list">
      <li class="media-item"><div class="media-thumb m2" role="img" aria-label="Video project photo"></div><div><strong>Curabitur ornare</strong><span>August 3rd, 2015</span></div></li>
      <li class="media-item"><div class="media-thumb m3" role="img" aria-label="Video project photo"></div><div><strong>Curabitur ornare</strong><span>August 3rd, 2015</span></div></li>
      <li class="media-item"><div class="media-thumb m1" role="img" aria-label="Video project photo"></div><div><strong>Curabitur ornare</strong><span>August 3rd, 2015</span></div></li>
    </ul>
  </div>
</section>

<section class="reviews">
  <h2 class="section-title">Customer Reviews</h2>
  <div class="review-grid">
    <article class="review">
      <h3><svg width="12" height="12" viewBox="0 0 12 12"><circle cx="6" cy="6" r="6" fill="#bbb"/><path d="M5 3.5 7.5 6 5 8.5" stroke="#fff" stroke-width="1.4" fill="none"/></svg>"Lumera 525 Projector"</h3>
      <div class="review-meta"><span>February 8th, 2015</span><span>12</span></div>
      <p>Integer aliquam felis sem, id finibus ut porta nisi lorem.</p>
    </article>
    <article class="review">
      <h3><svg width="12" height="12" viewBox="0 0 12 12"><circle cx="6" cy="6" r="6" fill="#bbb"/><path d="M5 3.5 7.5 6 5 8.5" stroke="#fff" stroke-width="1.4" fill="none"/></svg>"Brightwall Board tune-ups"</h3>
      <div class="review-meta"><span>February 8th, 2015</span><span>12</span></div>
      <p>Integer aliquam felis sem, id finibus ut porta nisi lorem.</p>
    </article>
    <article class="review">
      <h3><svg width="12" height="12" viewBox="0 0 12 12"><circle cx="6" cy="6" r="6" fill="#bbb"/><path d="M5 3.5 7.5 6 5 8.5" stroke="#fff" stroke-width="1.4" fill="none"/></svg>"Professional Service Provider"</h3>
      <div class="review-meta"><span>February 8th, 2015</span><span>12</span></div>
      <p>Integer aliquam felis sem, id finibus ut porta nisi lorem.</p>
    </article>
  </div>
</section>

<span class="to-top">TOP</span>
<footer class="site-footer">Copyright © 2015 Kelvaro Supply. All Rights Reserved</footer>

</body>
</html>
```